New Business Card Design Project

Use the flyer uploaded and website www.brightoakbuilders.com for inspiration.
List Our Services on Backside of business cards
Marcus Delling
Harborline Builders Inc.
Licensed General Contractors
858-471-6093

Contact Information for Business Card

Use the flyer uploaded and website www.brightoakbuilders.com for inspiration. List Our Services on Backside of business cards Marcus Delling Harborline Builders Inc. Licensed General Contractors 858-471-6093

```html
<!DOCTYPE html>
<html lang="en">
<head>
<meta charset="utf-8">
<title>Harborline Builders – Business Card</title>
<link href="https://fonts.googleapis.com/css2?family=Marcellus&family=Montserrat:wght@400;500&display=swap" rel="stylesheet">
<style>
  :root {
    --canvas: #e9e9e9;
    --card-light: #ffffff;
    --card-dark: #1f1f1f;
    --ink: #111111;
    --ink-soft: #333333;
    --paper-text: #f2f2f2;
    --rule-dark: #bdbdbd;
  }
  * { box-sizing: border-box; margin: 0; padding: 0; }
  html, body {
    width: 1200px; height: 900px; overflow: hidden;
    background: var(--canvas);
  }
  .sheet {
    width: 1200px; height: 900px;
    display: flex; flex-direction: column;
    align-items: center; justify-content: center; gap: 48px;
  }
  .card {
    position: relative;
    width: 660px; height: 377px;
    border-radius: 26px;
    box-shadow: 0 10px 30px rgba(0,0,0,.18);
    overflow: hidden;
  }

  /* Front */
  .card--front { background: var(--card-light); color: var(--ink); }
  .holder { position: absolute; left: 46px; top: 58px; }
  .holder__name {
    font-family: "Marcellus", serif;
    font-size: 30px; letter-spacing: 1px; text-transform: uppercase;
  }
  .holder__role {
    font-family: "Montserrat", sans-serif;
    font-size: 15px; color: var(--ink-soft); margin-top: 2px;
  }
  .brand {
    font-family: "Marcellus", serif;
    text-transform: uppercase; letter-spacing: 2px;
  }
  .card--front .brand {
    position: absolute; right: 46px; top: 150px;
    font-size: 28px; color: var(--ink);
  }
  .contact {
    position: absolute; right: 46px; bottom: 46px;
    list-style: none;
    font-family: "Montserrat", sans-serif; font-size: 16px;
    display: flex; flex-direction: column; gap: 9px;
  }
  .contact__item { display: flex; align-items: center; gap: 10px; }
  .contact__icon { width: 15px; height: 15px; flex: none; }

  /* Back */
  .card--back { background: var(--card-dark); color: var(--paper-text); }
  .rule {
    position: absolute; height: 1px; background: var(--rule-dark);
  }
  .rule--top { top: 56px; left: 70px; right: 40px; }
  .rule--bottom { bottom: 56px; left: 40px; right: 70px; }
  .card--back .brand {
    position: absolute; left: 0; right: 0; top: 110px;
    text-align: center; font-size: 34px;
  }
  .services {
    position: absolute; left: 0; right: 0; top: 205px;
    text-align: center;
    font-family: "Montserrat", sans-serif; font-size: 18px; line-height: 1.6;
  }
</style>
</head>
<body>
<main class="sheet">

  <section class="card card--front" aria-label="Business card front">
    <div class="holder">
      <h1 class="holder__name">Marcus Delling</h1>
      <p class="holder__role">Licensed General Contractors</p>
    </div>

    <p class="brand">Harborline Builders</p>

    <ul class="contact">
      <li class="contact__item">
        <svg class="contact__icon" viewBox="0 0 24 24" aria-hidden="true"><path fill="#111" d="M6.6 10.8a15.1 15.1 0 0 0 6.6 6.6l2.2-2.2a1 1 0 0 1 1-.25 11.4 11.4 0 0 0 3.6.57 1 1 0 0 1 1 1V20a1 1 0 0 1-1 1A17 17 0 0 1 3 4a1 1 0 0 1 1-1h3.5a1 1 0 0 1 1 1c0 1.25.2 2.46.57 3.6a1 1 0 0 1-.25 1z"/></svg>
        858-471-6093
      </li>
      <li class="contact__item">
        <svg class="contact__icon" viewBox="0 0 24 24" aria-hidden="true"><path fill="#111" d="M2 5h20v14H2z"/><path fill="none" stroke="#fff" stroke-width="1.6" d="M2.5 5.5 12 13l9.5-7.5"/></svg>
        info@brightoakbuilders.com
      </li>
      <li class="contact__item">
        <svg class="contact__icon" viewBox="0 0 24 24" aria-hidden="true"><circle cx="12" cy="12" r="10" fill="none" stroke="#111" stroke-width="2"/><path fill="none" stroke="#111" stroke-width="1.6" d="M2 12h20M12 2c3 3 3 17 0 20M12 2c-3 3-3 17 0 20"/></svg>
        www.brightoakbuilders.com
      </li>
    </ul>
  </section>

  <section class="card card--back" aria-label="Business card back">
    <span class="rule rule--top"></span>
    <p class="brand">Harborline Builders</p>
    <p class="services">
      Painting • Flooring • Kitchens • Custom Renovations<br>
      Bathrooms • Energy Efficient Upgrades
    </p>
    <span class="rule rule--bottom"></span>
  </section>

</main>
</body>
</html>
```